A gateway to the eyes of potential Talquen Candidates and Clients

We are looking for a brochure that will grab attention, all most along the lines of an infogram. The business supplies people to the construction sector. So we want it simple but sharp.

I would like the brochure to be able to have a half fold effect when printed but the main focus will be to use it in an e-brochure format.

Main pages will be as follows:

About Us: Which will have a bit about the management team and some pictures.

Services: information for both candidate and clients.

Why us?:

Contact: Location, contact numbers etc.

FOR CONTENTS:
website will give you the content required. www.talquenbuilders.co.uk
Updates

Project Deadline Extended Reason: Project was moved from a flyer to a brochure and the logo didn't upload. So I will be uploading my new logo and it will give additional time to get designs in. Cheers Added Monday, June 20, 2016

Target Market(s)

Clients and candidates for the construction market

Industry/Entity Type

Business

Requirements
Must have
• Bold and strong images of the construction sector. A simple to read format. Also needs to look good in an electronic format.
Nice to have
• I like the idea of a black and white model but with certain parts of the images highlighted in our colours.
Should not have
• Too much of a complex lay out.

```html
<!DOCTYPE html>
<html lang="en">
<head>
<meta charset="utf-8">
<title>Talquen Construction – Brochure Cover</title>
<link href="https://fonts.googleapis.com/css2?family=Exo+2:wght@600&family=Open+Sans:wght@400;600&display=swap" rel="stylesheet">
<style>
  :root {
    --page-bg: #ece8e2;
    --blue-deep: #0d5fa8;
    --blue-mid: #1586d0;
    --blue-light: #2a9be0;
    --blue-dark: #0b4f93;
    --orange: #f39a12;
    --orange-deep: #e77d0c;
    --paper: #f7f7f7;
    --ink: #333a40;
    --rule: #8a9098;
  }
  * { box-sizing: border-box; margin: 0; padding: 0; }
  html, body { width: 1200px; height: 804px; overflow: hidden; background: var(--page-bg); }
  .canvas { position: relative; width: 1200px; height: 804px; }
  .cover {
    position: absolute; left: 330px; top: 20px; width: 540px; height: 764px;
    background: var(--paper); overflow: hidden;
    box-shadow: 0 6px 18px rgba(0,0,0,.18);
    font-family: "Open Sans", sans-serif;
  }
  .cover__stripe { position: absolute; left: 0; top: 0; width: 100%; height: 9px;
    background: linear-gradient(90deg, var(--orange-deep), var(--orange)); }
  .cover__header {
    position: absolute; left: 0; top: 9px; width: 100%; height: 300px;
    background: radial-gradient(ellipse at 55% 35%, var(--blue-light), var(--blue-mid) 45%, var(--blue-deep));
  }
  .cover__title {
    position: absolute; left: 60px; top: 128px;
    font-family: "Exo 2", sans-serif; font-weight: 600; font-size: 38px; letter-spacing: .5px;
    color: #fff; white-space: nowrap;
  }
  .cover__title-name { color: var(--orange); margin-right: 10px; }
  .cover__strapline {
    position: absolute; left: 62px; top: 186px; font-size: 9.5px; color: #e6f1fa; white-space: nowrap;
  }
  .cover__photo {
    position: absolute; left: 40px; top: 262px; width: 500px; height: 270px;
    background: linear-gradient(170deg, #cfe2f2 0%, #a9c8e6 40%, #6f93b8 62%, #c9d34a 78%, #8d9a55 100%);
    clip-path: polygon(0 22%, 100% 0, 100% 100%, 0 100%);
  }
  .tile { position: absolute; }
  .tile--orange-top { left: 0; top: 360px; width: 78px; height: 70px;
    background: linear-gradient(135deg, var(--orange), var(--orange-deep)); }
  .tile--navy { left: 95px; top: 410px; width: 85px; height: 80px; background: var(--blue-dark); }
  .tile--blue-left { left: 40px; top: 490px; width: 85px; height: 80px; background: var(--blue-light); }
  .tile--blue-right { left: 455px; top: 375px; width: 85px; height: 78px; background: var(--blue-light); }
  .tile--orange-bottom { left: 390px; top: 460px; width: 90px; height: 85px;
    background: linear-gradient(135deg, var(--orange), var(--orange-deep)); }
  .brand {
    position: absolute; left: 60px; top: 612px; display: flex; align-items: center; gap: 8px;
  }
  .brand__mark { width: 22px; height: 22px; background: var(--orange); }
  .brand__name { font-weight: 600; font-size: 17px; color: var(--orange); letter-spacing: 1px; }
  .cover__tagline {
    position: absolute; left: 190px; top: 606px; font-size: 17px; color: var(--ink);
  }
  .cover__rule { position: absolute; left: 40px; width: 460px; height: 1px; background: var(--rule); }
  .cover__rule--top { top: 655px; }
  .cover__rule--bottom { top: 700px; }
  .contact {
    position: absolute; left: 60px; top: 668px; display: flex; gap: 14px;
    font-size: 11px; color: var(--ink); white-space: nowrap;
  }
  .contact__sep { color: var(--rule); }
</style>
</head>
<body>
<div class="canvas">
  <section class="cover">
    <div class="cover__stripe"></div>
    <header class="cover__header">
      <h1 class="cover__title"><span class="cover__title-name">TALQUEN</span>CONSTRUCTION</h1>
      <p class="cover__strapline">Fresh start? New Job? Brighter Future? A Better you? Talquen Construction is in your corner.</p>
    </header>
    <div class="cover__photo" role="img" aria-label="Photo of two construction workers in hard hats and hi-vis vests reviewing plans beneath a crane"></div>
    <div class="tile tile--orange-top"></div>
    <div class="tile tile--navy"></div>
    <div class="tile tile--blue-left"></div>
    <div class="tile tile--blue-right"></div>
    <div class="tile tile--orange-bottom"></div>
    <div class="brand">
      <span class="brand__mark"></span>
      <span class="brand__name">TALQUEN</span>
    </div>
    <p class="cover__tagline">Be a better version of you...</p>
    <div class="cover__rule cover__rule--top"></div>
    <div class="contact">
      <span>www.talquenbuilders.co.uk</span><span class="contact__sep">|</span>
      <span>info@talquenbuilders.co.uk</span><span class="contact__sep">|</span>
      <span>01632 960415</span>
    </div>
    <div class="cover__rule cover__rule--bottom"></div>
  </section>
</div>
</body>
</html>
```